CoinHarbor.com Site Redesign

We are looking to redesign our CoinHarbor.com site. This site is focused on helping consumers make smart financial decisions. We provide reviews and articles in various categories.

We are looking for a responsive design to run on wordpress. We will also have adsense advertisements on our page and will want some ad spot space. We are thinking of two column design vs. single column.

Here is an example of what our competitors look like:
ShopperBeacon.org (mostly reviews vs. articles)
Homepage - https://www.shopperbeacon.example/
Category Review Listing - https://www.shopperbeacon.example/mortgage-refinance/best-mortgage-refinance
Individual Review - https://www.shopperbeacon.example/mortgage-refinance/c/loan-orchard-mortgage-refinance-review

- I like that the site is extremely clean. I like the fixed header in mobile

PilotGuide
Homepage - https://www.pilotguide.example/
Category Review Listing-https://www.pilotguide.example/auto_insurance/index.php
Individual Review- https://www.pilotguide.example/auto_insurance/drivora_review.php

Articles - https://www.pilotguide.example/blog/2017/11/20/going-on-a-holiday-road-trip-be-prepared-for-these-hazards/

What I Like? I like the two column layout in that it gives room for advertising.
What I Do NOT Like? The top navigation is a little cumbersome and old. Mobile view is not very good. Content seems a bit cluttered.

PennyMoth
Homepage - https://www.pennymoth.example
Category Review Listing - https://www.pennymoth.example/blog/insurance/best-car-insurance-companies/?trk=pm_gn1_4.0
Individual Review- https://www.pennymoth.example/blog/insurance/veloro-insurance-review/

What I Like? very clean. Like the use of white space and focus on bright color call to action buttons.
What I Do NOT Like? In mobile a lot of content is pushed below the fold because of the large image above the fold. Reviews are not well organized.

Target Market(s)

consumers interested in saving money and making smart financial decisions

Industry/Entity Type

Financial

Logo Text

CoinHarbor.com or CoinHarbor

Coding

Coded - Design and coding required

Number of Pages Required

5+ page

Font styles to use
Sans Serif

Colors

Designer to choose colors to be used in the design.

Requirements
Must have
• -responsive design
• -room for ad space in the right column
Nice to have
• -good use of white space
• -clean layouts
Should not have
• -clutter

```html
<!DOCTYPE html>
<html lang="en">
<head>
<meta charset="utf-8">
<title>CoinHarbor.com – Make smarter financial decisions</title>
<link href="https://fonts.googleapis.com/css2?family=Lato:wght@400;700;900&display=swap" rel="stylesheet">
<style>
:root{
  --navy:#0e2d6e;
  --blue:#1a7cc2;
  --link:#1f7bc9;
  --orange:#e8661b;
  --ink:#333;
  --muted:#555;
  --band:#f1f1f1;
  --footer-dark:#2b2b2b;
  --white:#fff;
}
*{box-sizing:border-box;margin:0;padding:0}
html,body{width:1200px;height:2469px;overflow:hidden}
body{font-family:'Lato',sans-serif;color:var(--ink);background:var(--white);position:relative}
a{text-decoration:none;color:inherit}

/* Header */
.site-header{height:97px;position:relative;background:var(--white)}
.brand{position:absolute;left:74px;top:30px;display:flex;align-items:center;gap:10px;font-size:25px;font-weight:700;color:var(--navy)}
.brand-mark{width:26px;height:26px;background:var(--blue)}
.main-nav{position:absolute;left:359px;top:42px;display:flex;font-size:14px;font-weight:700;color:#333;letter-spacing:.3px}
.main-nav a{margin-right:0}
.nav-cat{width:155px}
.nav-cat::after{content:"";display:inline-block;margin-left:10px;border:5px solid transparent;border-top:7px solid #333;vertical-align:-4px}
.nav-item:nth-child(2){width:123px}
.nav-item:nth-child(3){width:89px}
.nav-item:nth-child(4){width:97px}
.btn{display:inline-block;background:var(--orange);color:var(--white);font-weight:700;text-align:center}
.btn-login{position:absolute;left:946px;top:34px;width:160px;height:32px;line-height:32px;font-size:14px}

/* Hero */
.hero{position:relative;height:387px;text-align:center;color:var(--white)}
.hero-bg{position:absolute;inset:0;background:linear-gradient(100deg,#6d6f74 0%,#8a8580 35%,#9a6b6b 55%,#b9b7b6 80%,#d6d6d6 100%)}
.hero-bg::after{content:"";position:absolute;inset:0;background:rgba(0,0,0,.28)}
.hero-content{position:relative;padding-top:90px}
.hero h1{font-size:50px;font-weight:900;line-height:58px}
.hero-sub{font-size:19px;font-weight:700;margin-top:2px;letter-spacing:.3px}
.search{margin:20px auto 0;width:568px;height:48px;border-radius:24px;background:var(--white);border:3px solid #444;color:#222;font-size:25px;font-weight:700;line-height:42px}
.search span{color:#777}
.disclosure{font-size:14px;font-weight:700;margin-top:18px}
.disclosure a{color:#4aa3ff;text-decoration:underline}

/* Categories */
.categories{position:absolute;left:74px;top:527px;width:1050px;display:grid;grid-template-columns:repeat(4,252px);gap:16px 14px}
.tile{height:176px;display:flex;align-items:center;justify-content:center;color:var(--white);font-size:18px;font-weight:700}
.t1{background:linear-gradient(#3c4d6b,#5a4d54)}
.t2{background:linear-gradient(#8c6a5b,#5e4a40)}
.t3{background:linear-gradient(#a8b4bd,#7d8a94)}
.t4{background:linear-gradient(#3f5a8a,#2d2f3a)}
.t5{background:linear-gradient(#6c6760,#3f3b36)}
.t6{background:linear-gradient(#566a45,#3e4a33)}
.t7{background:linear-gradient(#9aa8b0,#6d7b84)}
.t8{background:linear-gradient(#6a6a6a,#3b3b3b)}

/* Editorial process */
.editorial{position:absolute;left:0;top:895px;width:1200px;height:384px;background:linear-gradient(#fff 40%,#f6f6f6)}
.editorial h2{position:absolute;top:52px;width:100%;text-align:center;font-size:27px;font-weight:700;color:#333}
.step{position:absolute;top:147px;width:320px;text-align:center}
.step-icon{width:92px;height:92px;border:3px solid var(--navy);border-radius:50%;margin:0 auto;display:flex;align-items:center;justify-content:center}
.step h3{margin-top:20px;font-size:19px;color:var(--navy);font-weight:700}
.step p{font-size:15.5px;line-height:26px;color:var(--ink);margin-top:2px}
.s1{left:80px}.s2{left:441px}.s3{left:798px}

/* Articles */
.articles{position:absolute;left:0;top:1279px;width:1200px;height:599px;background:var(--band);border-top:1px solid #e2e2e2}
.articles h2{position:absolute;left:74px;top:38px;font-size:27px;font-weight:700;letter-spacing:.3px;color:#333}
.arrows{position:absolute;left:1082px;top:44px}
.card{position:absolute;top:97px;width:331px}
.c1{left:74px}.c2{left:435px}.c3{left:793px}
.card-img{height:183px}
.ci1{background:linear-gradient(#d9d6cb,#8d8e86)}
.ci2{background:linear-gradient(90deg,#4d5a2c,#8a8c3f,#5b6b2f)}
.ci3{background:linear-gradient(#c9c2b8,#e8e4dd)}
.card h3{margin-top:17px;font-size:20px;line-height:25px;color:var(--navy);font-weight:700}
.author{display:flex;align-items:center;gap:10px;margin-top:10px;font-size:15px;color:#222}
.avatar{width:30px;height:30px;border-radius:50%;background:#9a9a9a}
.card p{margin-top:10px;font-size:14.5px;line-height:24px;color:var(--ink)}
.card p a{color:var(--link);font-weight:700}
.btn-more{position:absolute;left:520px;top:533px;width:160px;height:33px;line-height:33px;font-size:14px}

/* Subscribe */
.subscribe{position:absolute;left:0;top:1878px;width:1200px;height:212px;background:var(--blue);text-align:center;color:var(--white)}
.subscribe h2{margin-top:32px;font-size:29px;font-weight:700}
.subscribe p{margin-top:8px;font-size:16px}
.email{position:relative;margin:20px auto 0;width:450px;height:46px;border-radius:23px;background:var(--white);text-align:left;padding-left:20px;line-height:46px;color:#555;font-size:14px}
.email-go{position:absolute;right:4px;top:4px;width:38px;height:38px;border-radius:50%;background:var(--navy);color:var(--white);text-align:center;line-height:38px;font-weight:700;font-size:15px}

/* Footer */
.site-footer{position:absolute;left:0;top:2090px;width:1200px;height:313px}
.footer-col h4{position:absolute;top:30px;font-size:16px;color:var(--navy);font-weight:700}
.link-list{position:absolute;top:60px;list-style:none;font-size:14px;line-height:28.6px;color:var(--ink)}
.footer-text{position:absolute;left:790px;top:60px;width:340px;font-size:14px;line-height:23px;color:var(--ink)}
.follow{position:absolute;left:790px;top:220px;font-size:16px;color:var(--navy);font-weight:700}
.social{position:absolute;left:790px;top:255px;display:flex;gap:22px}
.social span{width:22px;height:22px;border-radius:50%;background:#333}
.bottom-bar{position:absolute;left:0;top:2403px;width:1200px;height:66px;background:var(--footer-dark);color:#bbb;font-size:12.5px}
.bottom-bar .copy{position:absolute;left:74px;top:26px}
.bottom-bar .legal{position:absolute;right:76px;top:30px}
</style>
</head>
<body>

<header class="site-header">
  <a class="brand" href="#"><span class="brand-mark"></span>CoinHarbor.com</a>
  <nav class="main-nav">
    <a class="nav-cat" href="#">All Categories</a>
    <a class="nav-item" href="#">CREDIT CARDS</a>
    <a class="nav-item" href="#">BANKING</a>
    <a class="nav-item" href="#">INVESTING</a>
    <a class="nav-item" href="#">MORTGAGES</a>
  </nav>
  <a class="btn btn-login" href="#">JOIN OR LOGIN</a>
</header>

<section class="hero">
  <div class="hero-bg" role="img" aria-label="Couple smiling while reviewing finances on a laptop"></div>
  <div class="hero-content">
    <h1>Make smarter financial decisions</h1>
    <p class="hero-sub">FIND THE BEST FINANCIAL PRODUCTS &amp; SERVICES</p>
    <div class="search">I'm looking for <span>product and category</span></div>
    <p class="disclosure">Disclosure: We receive advertising revenue from some partners. <a href="#">Learn more</a></p>
  </div>
</section>

<section class="categories">
  <a class="tile t1" href="#" role="img" aria-label="Hands protecting a piggy bank">Mortgage Refinance</a>
  <a class="tile t2" href="#" role="img" aria-label="Woman walking on a shopping street">Personal Loans</a>
  <a class="tile t3" href="#" role="img" aria-label="Nurse at a medical desk">Medical Alerts</a>
  <a class="tile t4" href="#" role="img" aria-label="Modern house at dusk">Home Security</a>
  <a class="tile t5" href="#" role="img" aria-label="Reverse mortgage form on a desk">Reverse Mortgages</a>
  <a class="tile t6" href="#" role="img" aria-label="Dog sitting on grass">Pet Insurance</a>
  <a class="tile t7" href="#" role="img" aria-label="Patient in a dental chair">Dental Insurance</a>
  <a class="tile t8" href="#" role="img" aria-label="Woman holding a credit card at a laptop">Credit Repair</a>
</section>

<section class="editorial">
  <h2>Our Editorial Process</h2>
  <div class="step s1">
    <div class="step-icon"><svg width="36" height="30" viewBox="0 0 36 30"><rect x="1" y="1" width="34" height="28" fill="none" stroke="#0e2d6e" stroke-width="2.5"/><rect x="8" y="14" width="4" height="10" fill="#0e2d6e"/><rect x="15" y="8" width="4" height="16" fill="#0e2d6e"/><rect x="22" y="11" width="4" height="13" fill="#0e2d6e"/></svg></div>
    <h3>We Analyze &amp; Explain</h3>
    <p>We analyze &amp; explain how each online<br>service works.</p>
  </div>
  <div class="step s2">
    <div class="step-icon"><svg width="30" height="36" viewBox="0 0 30 36"><path d="M2 2h18l8 8v24H2z" fill="#0e2d6e"/><path d="M20 2v8h8" fill="#fff" opacity=".5"/><rect x="8" y="15" width="14" height="2.5" fill="#fff"/><rect x="8" y="21" width="14" height="2.5" fill="#fff"/><rect x="8" y="27" width="14" height="2.5" fill="#fff"/></svg></div>
    <h3>We Test &amp; Compare</h3>
    <p>We test &amp; compare the leading services in<br>each category</p>
  </div>
  <div class="step s3">
    <div class="step-icon"><svg width="32" height="30" viewBox="0 0 32 30"><rect x="1" y="12" width="7" height="16" fill="#0e2d6e"/><path d="M10 13l7-11c3 0 4 2 3 5l-1 4h9c2 0 3 2 2 4l-3 11c-1 2-2 2-4 2H10z" fill="#0e2d6e"/></svg></div>
    <h3>We Review &amp; Rate</h3>
    <p>We review and rate each service to show<br>which is best</p>
  </div>
</section>

<section class="articles">
  <h2>GUIDES &amp; ARTICLES FROM OUR EDITORS</h2>
  <div class="arrows"><svg width="42" height="20" viewBox="0 0 42 20"><path d="M10 2L3 10l7 8" fill="none" stroke="#333" stroke-width="3"/><path d="M32 2l7 8-7 8" fill="none" stroke="#333" stroke-width="3"/></svg></div>

  <article class="card c1">
    <div class="card-img ci1" role="img" aria-label="Rolled banknotes held by a rubber band"></div>
    <h3>5 “Easy” Ways Parents Can Save $1000’s a Year</h3>
    <div class="author"><span class="avatar"></span>By Dana Pryor</div>
    <p>Parents, let’s face it – the high cost of raising children leaves us all needing a little extra money. Short of getting a big raise, switching jobs, or winning... <a href="#">Read More</a></p>
  </article>
  <article class="card c2">
    <div class="card-img ci2" role="img" aria-label="Two riders on a motorcycle"></div>
    <h3>Motorcycle Insurance Basics</h3>
    <div class="author"><span class="avatar"></span>By Dana Pryor</div>
    <p>Motorcycle insurance can be quite expensive; it can be the same amount as an auto insurance quote in some cases. Depending on the coverage you select and your driving... <a href="#">Read More</a></p>
  </article>
  <article class="card c3">
    <div class="card-img ci3" role="img" aria-label="Car key and banknotes on an auto insurance policy"></div>
    <h3>How Do I Get Cheap Auto Insurance?</h3>
    <div class="author"><span class="avatar"></span>By Dana Pryor</div>
    <p>If you’re looking for cheap auto insurance, then you aren’t alone. Many drivers regularly search for lower cost, more affordable insurance for their vehicles on a regular basis. If...... <a href="#">Read More</a></p>
  </article>

  <a class="btn btn-more" href="#">MORE ARTICLES</a>
</section>

<section class="subscribe">
  <h2>Email Subscribe</h2>
  <p>Subscribe To Our Newsletter To Get The Latest Great Deals And Reviews</p>
  <div class="email">Enter Email Address<span class="email-go">Go</span></div>
</section>

<footer class="site-footer">
  <div class="footer-col">
    <h4 style="left:74px">All Services Reviewed</h4>
    <ul class="link-list" style="left:74px">
      <li>Annuities</li><li>Auto Insurance</li><li>Credit Monitoring</li><li>Credit Repair</li><li>Debt Management</li><li>Homeowners Insurance</li><li>Identity Theft</li><li>Life Insurance</li>
    </ul>
    <ul class="link-list" style="left:252px">
      <li>Mortgages</li><li>Online Brokerages</li><li>Payday Loans</li><li>Personal Finance</li><li>Student Loan Consolidation</li><li>Tax Settlement</li>
    </ul>
  </div>
  <div class="footer-col">
    <h4 style="left:502px">Popular Services Reviewed</h4>
    <ul class="link-list" style="left:502px">
      <li>Debt Management</li><li>Payday Loans</li><li>Credit Cards</li>
    </ul>
  </div>
  <div class="footer-col">
    <h4 style="left:790px">Advertising Disclosure:</h4>
    <p class="footer-text">CoinHarbor.com is an independent advertising supported comparison service. CoinHarbor.com may be compensated in exchange for featured placement of certain sponsored products and services, or your clicking on links posted on this website.</p>
    <p class="follow">Follow Us</p>
    <div class="social"><span></span><span></span><span></span><span></span><span></span></div>
  </div>
</footer>

<div class="bottom-bar">
  <span class="copy">Copyright © 2017 CoinHarbor. All rights reserved.</span>
  <span class="legal">About us / Privacy Policy / Terms of Service / Contact us</span>
</div>

</body>
</html>
```